Vision, Mission and Culture Posters

We have written text paragraphs for our company vision and mission and need them made into a2 or a3 sized posters using our logo for inspiration for colour. Our company culture has 10 paragraphs and we'd like this to be a single poster of a2 or a1. Each poster should have the logo on and share common design. It's not a complex job really.

Industry/Entity Type

It Company

Requirements
Nice to have
• These will be going up on our office wall so need to be clear to read from a distance and look professional but also not stodgy.

```html
<!DOCTYPE html>
<html lang="en">
<head>
<meta charset="utf-8">
<title>Our Mission – Lotwise Parking</title>
<link href="https://fonts.googleapis.com/css2?family=Montserrat:wght@700&family=Open+Sans:ital,wght@0,400;0,600;0,700;1,700&display=swap" rel="stylesheet">
<style>
  :root {
    --paper: #f3f3f4;
    --lime-light: #f2ea2a;
    --lime-dark: #a19e1c;
    --orange: #f15a2b;
    --amber: #fbb040;
    --brand-yellow: #f7ec21;
    --ink: #1f1f20;
    --charcoal: #3d3e40;
    --red: #ee3d3a;
    --white: #ffffff;
  }
  * { margin: 0; padding: 0; box-sizing: border-box; }
  html, body { width: 848px; height: 1200px; overflow: hidden; background: var(--paper); }
  .poster {
    position: relative;
    width: 848px;
    height: 1200px;
    overflow: hidden;
    background: var(--paper);
    font-family: "Open Sans", Arial, sans-serif;
    color: var(--ink);
  }
  .backdrop { position: absolute; inset: 0; }
  .poster-title {
    position: absolute;
    top: 28px; left: 0; width: 100%;
    text-align: center;
    font-family: "Montserrat", Arial, sans-serif;
    font-weight: 700;
    font-size: 52px;
    color: var(--white);
    text-shadow: 0 0 2px #555, 1px 1px 0 #666;
  }
  .brand-plate {
    position: absolute;
    left: 226px; top: 160px;
    width: 392px; height: 112px;
    background: var(--brand-yellow);
    border-radius: 8px;
    box-shadow: 3px 4px 5px rgba(0,0,0,.35);
    display: flex; align-items: center; justify-content: center; gap: 16px;
  }
  .brand-square { width: 30px; height: 30px; background: var(--ink); }
  .brand-name { font-weight: 700; font-size: 30px; color: var(--ink); letter-spacing: 1px; }
  .line { position: absolute; line-height: 1; white-space: nowrap; }
  .lead { font-weight: 700; font-size: 56px; color: var(--charcoal); letter-spacing: -1px; }
  .lead small { font-weight: 400; font-size: 30px; color: var(--charcoal); letter-spacing: 0; }
  .accent { font-weight: 700; color: var(--red); }
  .accent-italic { font-style: italic; }
  .heading { font-weight: 700; color: var(--charcoal); }
  .body { font-weight: 400; color: var(--ink); }
  .spaced { letter-spacing: 2px; }
  .closing {
    position: absolute;
    right: 44px; top: 766px;
    text-align: right;
    font-size: 20px; line-height: 26px;
    color: var(--charcoal);
  }
</style>
</head>
<body>
<main class="poster">
  <svg class="backdrop" width="848" height="1200" viewBox="0 0 848 1200" aria-hidden="true">
    <defs>
      <linearGradient id="lime" x1="0" y1="0" x2="1" y2="0">
        <stop offset="0" stop-color="var(--lime-light)"/>
        <stop offset="1" stop-color="var(--lime-dark)"/>
      </linearGradient>
      <linearGradient id="warm" x1="0" y1="0" x2="1" y2="0">
        <stop offset="0" stop-color="#f7941d"/>
        <stop offset="1" stop-color="var(--amber)"/>
      </linearGradient>
    </defs>
    <!-- top band -->
    <path d="M0 0 H848 V160 Q430 100 0 150 Z" fill="url(#lime)"/>
    <path d="M0 150 Q430 100 848 160 V178 Q430 118 0 168 Z" fill="var(--white)"/>
    <path d="M0 162 Q430 116 848 170 V180 Q430 130 0 178 Z" fill="var(--orange)"/>
    <!-- bottom bands -->
    <path d="M0 880 Q300 840 520 880 Q700 915 848 980 V1200 H0 Z" fill="var(--white)"/>
    <path d="M0 888 Q300 848 520 888 Q700 922 848 990 V1200 H0 Z" fill="url(#lime)"/>
    <path d="M0 1010 Q420 1000 848 1060 V1200 H0 Z" fill="var(--white)"/>
    <path d="M0 1018 Q420 1008 848 1068 V1200 H0 Z" fill="url(#warm)"/>
    <path d="M0 1100 Q450 1105 848 1160 V1200 H0 Z" fill="var(--white)"/>
    <path d="M0 1108 Q450 1113 848 1168 V1200 H0 Z" fill="var(--orange)"/>
  </svg>

  <h1 class="poster-title">OUR MISSION</h1>

  <div class="brand-plate">
    <span class="brand-square"></span>
    <span class="brand-name">Lotwise Parking</span>
  </div>

  <p class="line lead" style="left:22px; top:288px;">Our Mission<small>is to achieve</small></p>
  <p class="line accent" style="left:72px; top:350px; font-size:46px;">Great Customer Satisfaction</p>
  <p class="line body" style="left:113px; top:393px; font-size:27px;">In everything we do and offer for meeting</p>
  <p class="line heading" style="left:156px; top:427px; font-size:36px;">Our Customers’ Parking Needs.</p>
  <p class="line body" style="left:168px; top:474px; font-size:25px;">We believe our path to achieving this comes</p>
  <p class="line body" style="left:30px; top:514px; font-size:21px;">through giving a</p>
  <p class="line accent accent-italic" style="left:30px; top:537px; font-size:37px;">Simple Yet Thorough And Friendly Service</p>
  <p class="line body spaced" style="left:30px; top:582px; font-size:21px;">to our customers without unnecessary complication.</p>
  <p class="line body" style="left:84px; top:617px; font-size:22px;">We will achieve this through</p>
  <p class="line heading" style="left:84px; top:635px; font-size:42px;">Using The Technology Available</p>
  <p class="line body" style="left:86px; top:686px; font-size:21px;">to us, continual staff training and development,</p>
  <p class="line heading" style="left:428px; top:719px; font-size:34px;">Regular Refinement</p>
  <p class="closing">of our practices and processes along<br>with commitment to our roles and<br>the foundations for building<br>our success.</p>
</main>
</body>
</html>
```